Tour Guide in Israel business card

I am a tour guide in Israel (the holy land). Prior to it I have over 20 years high-tech business. My main (but not only) focus is working with business people that come to Israel and want to get a tour (usually short from few hours to 2 days). During my guiding I incorporate a lot of my know how of the Israeli business culture. I like to have a business card that I can present to anyone that is looking for a tour guide, but that business people will understand the additional value I can provide them during my tour.

Target Market(s)

Business visitors and tourist to Israel

Industry/Entity Type

Tourism

Contact Information for Business Card

Danny Korvath
email: danny@korvath-tours.example
Mobile: +972-52-7416205

Colors

Designer to choose colors to be used in the design.

Requirements
Must have
• Tour Guide
Nice to have
• I don't know how but it should project my understanding in business not just the tourist side of my knowledge.

```html
<!DOCTYPE html>
<html lang="en">
<head>
<meta charset="utf-8">
<title>Danny Korvath – Business Card</title>
<link href="https://fonts.googleapis.com/css2?family=Arimo:wght@400;700&family=Roboto+Condensed:wght@300;400&display=swap" rel="stylesheet">
<style>
  :root {
    --page: #d6d6d6;
    --paper: #f4f4f4;
    --brand-blue: #125e8c;
    --ink-grey: #5a5a5a;
    --night-top: #0f5e8e;
    --night-mid: #0b3d5e;
    --night-bottom: #061a28;
    --label-grey: #5d7a92;
    --glow: #4fc8f5;
  }
  html, body {
    margin: 0;
    padding: 0;
    overflow: hidden;
  }
  body {
    width: 1200px;
    height: 1047px;
    background: var(--page);
    position: relative;
  }
  .card {
    position: absolute;
    box-shadow: 0 1px 3px rgba(0,0,0,0.25);
    overflow: hidden;
  }
  /* Front */
  .card-front {
    left: 140px;
    top: 253px;
    width: 542px;
    height: 301px;
    background: var(--paper);
  }
  .band {
    position: absolute;
    left: 0;
    width: 100%;
    height: 47px;
    background: var(--brand-blue);
  }
  .band-top { top: 26px; }
  .band-bottom { top: 226px; }
  .contact-list {
    position: absolute;
    left: 46px;
    top: 107px;
    margin: 0;
    padding: 0;
    list-style: none;
    font-family: "Roboto Condensed", sans-serif;
    font-weight: 300;
    font-size: 18px;
    color: var(--ink-grey);
  }
  .contact-list li {
    display: flex;
    align-items: center;
    height: 28px;
  }
  .contact-icon {
    width: 18px;
    height: 18px;
    margin-right: 13px;
    fill: none;
    stroke: var(--brand-blue);
    stroke-width: 1.6;
  }
  .identity {
    position: absolute;
    right: 48px;
    top: 101px;
    text-align: right;
  }
  .name-first, .name-last {
    font-family: "Arimo", sans-serif;
    color: var(--brand-blue);
    line-height: 1;
    margin: 0;
  }
  .name-first {
    font-weight: 400;
    font-size: 29px;
    letter-spacing: 0.5px;
  }
  .name-last {
    font-weight: 700;
    font-size: 29px;
    letter-spacing: 1px;
    margin-top: 1px;
  }
  .role {
    font-family: "Roboto Condensed", sans-serif;
    font-weight: 300;
    font-size: 18px;
    color: var(--ink-grey);
    margin-top: 6px;
  }
  /* Back */
  .card-back {
    left: 759px;
    top: 253px;
    width: 302px;
    height: 541px;
    background: linear-gradient(180deg, var(--night-top) 0%, var(--night-mid) 45%, var(--night-bottom) 100%);
  }
  .network-map {
    position: absolute;
    left: 86px;
    top: 68px;
    width: 130px;
    height: 336px;
  }
  .theme-label {
    position: absolute;
    font-family: "Roboto Condensed", sans-serif;
    font-weight: 300;
    font-size: 16px;
    color: var(--label-grey);
    white-space: nowrap;
    transform-origin: center;
  }
  .label-land { left: 132px; top: 60px; transform: rotate(-15deg); }
  .label-history { left: 182px; top: 160px; transform: rotate(80deg); }
  .label-business { left: 164px; top: 262px; transform: rotate(90deg); }
  .label-people { left: 68px; top: 176px; transform: rotate(-65deg); }
  .label-culture { left: 48px; top: 293px; transform: rotate(-80deg); }
  .label-faith { left: 82px; top: 365px; transform: rotate(-80deg); }
  .tagline {
    position: absolute;
    left: 0;
    width: 100%;
    top: 471px;
    text-align: center;
    font-family: "Arimo", sans-serif;
    font-size: 17px;
    letter-spacing: 1px;
    color: var(--glow);
  }
</style>
</head>
<body>
  <section class="card card-front" aria-label="Business card front">
    <div class="band band-top"></div>
    <ul class="contact-list">
      <li>
        <svg class="contact-icon" viewBox="0 0 20 20" aria-hidden="true"><path d="M5 2 L8 5 L6.5 7.5 Q8 11.5 12.5 13.5 L15 12 L18 15 L15.5 18 Q7 17 2 5 Z" fill="var(--brand-blue)" stroke="none"/></svg>
        +972-52-7416205
      </li>
      <li>
        <svg class="contact-icon" viewBox="0 0 20 20" aria-hidden="true"><rect x="1.5" y="4" width="17" height="12" fill="var(--brand-blue)" stroke="none"/><path d="M1.5 4 L10 11 L18.5 4 M1.5 16 L7.5 10 M18.5 16 L12.5 10" stroke="var(--paper)" stroke-width="1.4"/></svg>
        danny@korvath-tours.example
      </li>
      <li>
        <svg class="contact-icon" viewBox="0 0 20 20" aria-hidden="true"><circle cx="10" cy="10" r="8"/><ellipse cx="10" cy="10" rx="3.5" ry="8"/><path d="M2 10 H18 M3.5 5.5 H16.5 M3.5 14.5 H16.5"/></svg>
        www.korvath-tours.example
      </li>
    </ul>
    <div class="identity">
      <p class="name-first">DANNY</p>
      <p class="name-last">KORVATH</p>
      <div class="role">Tour Leader &amp; Storyteller</div>
    </div>
    <div class="band band-bottom"></div>
  </section>

  <section class="card card-back" aria-label="Business card back">
    <svg class="network-map" role="img" aria-label="Glowing connected-dots network map of Israel" viewBox="0 0 130 336">
      <defs>
        <radialGradient id="mapGlow" cx="50%" cy="40%" r="60%">
          <stop offset="0%" stop-color="#4fc8f5" stop-opacity="0.55"/>
          <stop offset="60%" stop-color="#2a8fc4" stop-opacity="0.25"/>
          <stop offset="100%" stop-color="#0b3d5e" stop-opacity="0"/>
        </radialGradient>
      </defs>
      <ellipse cx="65" cy="168" rx="62" ry="166" fill="url(#mapGlow)"/>
    </svg>
    <span class="theme-label label-land">Land</span>
    <span class="theme-label label-history">History</span>
    <span class="theme-label label-business">Business</span>
    <span class="theme-label label-people">People</span>
    <span class="theme-label label-culture">Culture</span>
    <span class="theme-label label-faith">Faith</span>
    <div class="tagline">CONNECTING THE DOTS</div>
  </section>
</body>
</html>
```